Amber Ledger of Kite Keepers

Hi - I would like your help transforming my (terrible) drawing into a graphic that pops -using hex colors I'll give you - so that I can put it into stationary and on t-shirts or tote bags. My company, the Quillmark Institute, trains social change leaders (from the sectors in the periodic table) on how to lead large-scale change. I have this vision - the "periodic table" but these are the sectors that my clients work in. If you are having trouble reading my writing, I apologize. Our hex colors are: #114769, #76984C, #80B5CF (Seagull), #8F2C63 and Rangoon Black #191919. You don't need to use all of them, but it'd be good to be consistent with our overall branding. If you can't read my writing, I will send correct spelling. The "Quillmark" with the flowers on the bottom is for a separate design bid.

Target Market(s)

nonprofit, social entrepreneurs, philanthropy, leaders

Requirements
Must have
• clean, readable font. alignment to look like periodic table of elements. heart icon for love, cat face for cats.

```html
<!DOCTYPE html>
<html lang="en">
<head>
<meta charset="utf-8">
<title>Amber Ledger of Kite Keepers</title>
<link rel="stylesheet" href="https://fonts.googleapis.com/css2?family=Nunito:wght@800;900&display=swap">
<style>
  :root {
    --ink: #000000;
    --paper: #ffffff;
    --green-face: #74fc3c;
    --green-edge: #5aff33;
    --teal-face: #95fbd8;
    --teal-edge: #66ffcc;
    --purple-face: #7b139b;
    --purple-edge: #5a0f6e;
    --blue-face: #0a3d7a;
    --blue-edge: #1e56ad;
    --cat-tone: #3f6f60;
  }
  html, body {
    margin: 0;
    width: 1200px;
    height: 1043px;
    overflow: hidden;
    background: var(--paper);
  }
  .table-art {
    display: block;
    width: 1200px;
    height: 1043px;
    font-family: "Nunito", "Arial Rounded MT Bold", sans-serif;
  }
  .frame { fill: none; stroke: var(--ink); stroke-width: 26; }
  .label { font-size: 40px; font-weight: 800; text-anchor: end; }
  .symbol { font-size: 136px; font-weight: 900; }
  .tile--green .edge { fill: var(--green-edge); }
  .tile--green .face { fill: var(--green-face); }
  .tile--teal .edge { fill: var(--teal-edge); }
  .tile--teal .face { fill: var(--teal-face); }
  .tile--purple .edge { fill: var(--purple-edge); }
  .tile--purple .face { fill: var(--purple-face); }
  .tile--blue .edge { fill: var(--blue-edge); }
  .tile--blue .face { fill: var(--blue-face); }
  .tile--green text, .tile--teal text { fill: var(--ink); }
  .tile--purple text, .tile--blue text { fill: var(--paper); }
  .heart { fill: var(--paper); }
  .cat-spot { fill: var(--cat-tone); }
</style>
</head>
<body>
<svg class="table-art" viewBox="0 0 2048 1780" xmlns="http://www.w3.org/2000/svg" aria-label="Amber Ledger of Kite Keepers">

  <!-- row 1 -->
  <g class="tile tile--green" transform="translate(288,228)">
    <rect class="frame" x="-13" y="-13" width="252" height="248" rx="34"/>
    <rect class="edge" width="226" height="222" rx="12"/><rect class="face" width="194" height="190" rx="12"/>
    <text class="label" x="212" y="50">Anti-</text><text class="label" x="212" y="86">violaci</text>
    <text class="symbol" x="12" y="200">Av</text></g>
  <g class="tile tile--purple" transform="translate(1548,230)">
    <rect class="frame" x="-13" y="-13" width="252" height="248" rx="34"/>
    <rect class="edge" width="226" height="222" rx="12"/><rect class="face" width="194" height="190" rx="12"/>
    <text class="label" x="214" y="50">Belonging</text>
    <text class="symbol" x="16" y="200">B</text></g>

  <!-- row 2 -->
  <g class="tile tile--green" transform="translate(288,476)">
    <rect class="frame" x="-13" y="-13" width="252" height="248" rx="34"/>
    <rect class="edge" width="226" height="222" rx="12"/><rect class="face" width="194" height="190" rx="12"/>
    <text class="label" x="212" y="50">Earth</text><text class="label" x="212" y="86">Childha</text>
    <text class="symbol" x="14" y="198">Ec</text></g>
  <g class="tile tile--teal" transform="translate(540,476)">
    <rect class="frame" x="-13" y="-13" width="252" height="248" rx="34"/>
    <rect class="edge" width="226" height="222" rx="12"/><rect class="face" width="194" height="190" rx="12"/>
    <text class="label" x="214" y="50">Climate</text><text class="label" x="200" y="86">Chanja</text>
    <text class="symbol" x="14" y="198">Cc</text></g>
  <g class="tile tile--teal" transform="translate(792,476)">
    <rect class="frame" x="-13" y="-13" width="252" height="248" rx="34"/>
    <rect class="edge" width="226" height="222" rx="12"/><rect class="face" width="194" height="190" rx="12"/>
    <text class="label" x="214" y="50">Environm</text><text class="label" x="150" y="86">Justia</text>
    <text class="symbol" x="14" y="198">Ej</text></g>
  <g class="tile tile--teal" transform="translate(1044,476)">
    <rect class="frame" x="-13" y="-13" width="252" height="248" rx="34"/>
    <rect class="edge" width="226" height="222" rx="12"/><rect class="face" width="194" height="190" rx="12"/>
    <text class="label" x="214" y="50">Human</text><text class="label" x="190" y="86">Simta</text>
    <text class="symbol" x="14" y="198">Hs</text></g>
  <g class="tile tile--teal" transform="translate(1296,476)">
    <rect class="frame" x="-13" y="-13" width="252" height="248" rx="34"/>
    <rect class="edge" width="226" height="222" rx="12"/><rect class="face" width="194" height="190" rx="12"/>
    <text class="label" x="214" y="50">Halth</text><text class="label" x="182" y="86">Las</text>
    <text class="symbol" x="14" y="198">Hl</text></g>
  <g class="tile tile--purple" transform="translate(1548,476)">
    <rect class="frame" x="-13" y="-13" width="252" height="248" rx="34"/>
    <rect class="edge" width="226" height="222" rx="12"/><rect class="face" width="194" height="190" rx="12"/>
    <text class="label" x="214" y="50">Honsing</text>
    <text class="symbol" x="14" y="198">H</text></g>

  <!-- row 3 -->
  <g class="tile tile--green" transform="translate(288,724)">
    <rect class="frame" x="-13" y="-13" width="252" height="248" rx="34"/>
    <rect class="edge" width="226" height="222" rx="12"/><rect class="face" width="194" height="190" rx="12"/>
    <text class="label" x="212" y="50">Education</text>
    <text class="symbol" x="14" y="198">Ed</text></g>
  <g class="tile tile--teal" transform="translate(540,724)">
    <rect class="frame" x="-13" y="-13" width="252" height="248" rx="34"/>
    <rect class="edge" width="226" height="222" rx="12"/><rect class="face" width="194" height="190" rx="12"/>
    <text class="label" x="164" y="50">Attn</text><text class="label" x="214" y="86">Suncol</text>
    <text class="symbol" x="10" y="198">As</text></g>
  <g class="tile tile--teal" transform="translate(792,724)">
    <rect class="frame" x="-13" y="-13" width="252" height="248" rx="34"/>
    <rect class="edge" width="226" height="222" rx="12"/><rect class="face" width="194" height="190" rx="12"/>
    <text class="label" x="214" y="50">Social</text><text class="label" x="212" y="86">Justia</text>
    <text class="symbol" x="12" y="198">Sj</text></g>
  <g class="tile tile--teal" transform="translate(1044,724)">
    <rect class="frame" x="-13" y="-13" width="252" height="248" rx="34"/>
    <rect class="edge" width="226" height="222" rx="12"/><rect class="face" width="194" height="190" rx="12"/>
    <text class="label" x="196" y="50">Civil</text><text class="label" x="214" y="86">Risht</text>
    <text class="symbol" x="14" y="198">Cr</text></g>
  <g class="tile tile--teal" transform="translate(1296,724)">
    <rect class="frame" x="-13" y="-13" width="252" height="248" rx="34"/>
    <rect class="edge" width="226" height="222" rx="12"/><rect class="face" width="194" height="190" rx="12"/>
    <text class="label" x="214" y="50">Health</text><text class="label" x="210" y="86">Equita</text>
    <text class="symbol" x="14" y="198">He</text></g>
  <g class="tile tile--purple" transform="translate(1548,724)">
    <rect class="frame" x="-13" y="-13" width="252" height="248" rx="34"/>
    <rect class="edge" width="226" height="222" rx="12"/><rect class="face" width="194" height="190" rx="12"/>
    <text class="label" x="214" y="50">Jobs</text>
    <text class="symbol" x="14" y="198">J</text></g>

  <!-- row 4 -->
  <g class="tile tile--green" transform="translate(288,972)">
    <rect class="frame" x="-13" y="-13" width="252" height="248" rx="34"/>
    <rect class="edge" width="226" height="222" rx="12"/><rect class="face" width="194" height="190" rx="12"/>
    <text class="label" x="198" y="50">Animal</text><text class="label" x="212" y="86">Weifare</text>
    <text class="symbol" x="10" y="198">Aw</text></g>
  <g class="tile tile--teal" transform="translate(540,972)">
    <rect class="frame" x="-13" y="-13" width="252" height="248" rx="34"/>
    <rect class="edge" width="226" height="222" rx="12"/><rect class="face" width="194" height="190" rx="12"/>
    <text class="label" x="214" y="50">Cat</text>
    <rect class="cat-spot" x="14" y="80" width="166" height="128" rx="40" role="img" aria-label="Cat face icon"/></g>
  <g class="tile tile--teal" transform="translate(792,972)">
    <rect class="frame" x="-13" y="-13" width="252" height="248" rx="34"/>
    <rect class="edge" width="226" height="222" rx="12"/><rect class="face" width="194" height="190" rx="12"/>
    <text class="label" x="214" y="50">Racial</text><text class="label" x="210" y="86">Justia</text>
    <text class="symbol" x="14" y="198">Rj</text></g>
  <g class="tile tile--teal" transform="translate(1044,972)">
    <rect class="frame" x="-13" y="-13" width="252" height="248" rx="34"/>
    <rect class="edge" width="226" height="222" rx="12"/><rect class="face" width="194" height="190" rx="12"/>
    <text class="label" x="214" y="50">Inmijn</text><text class="label" x="196" y="86">Risht</text>
    <text class="symbol" x="12" y="198">Av</text></g>
  <g class="tile tile--teal" transform="translate(1296,972)">
    <rect class="frame" x="-13" y="-13" width="252" height="248" rx="34"/>
    <rect class="edge" width="226" height="222" rx="12"/><rect class="face" width="194" height="190" rx="12"/>
    <text class="label" x="214" y="50">Behavian</text><text class="label" x="138" y="86">Halth</text>
    <text class="symbol" x="14" y="198">Bh</text></g>
  <g class="tile tile--purple" transform="translate(1548,972)">
    <rect class="frame" x="-13" y="-13" width="252" height="248" rx="34"/>
    <rect class="edge" width="226" height="222" rx="12"/><rect class="face" width="194" height="190" rx="12"/>
    <text class="label" x="112" y="50">Inter-</text><text class="label" x="214" y="86">generation</text>
    <text class="symbol" x="14" y="198">Ig</text></g>

  <!-- values row -->
  <g class="tile tile--blue" transform="translate(290,1342)">
    <rect class="frame" x="-13" y="-13" width="298" height="246" rx="34"/>
    <rect class="edge" width="272" height="220" rx="12"/><rect class="face" width="242" height="190" rx="12"/>
    <text class="label" x="210" y="50">Love</text>
    <path class="heart" d="M66 205 C40 170 14 140 14 118 C14 96 30 82 50 82 C62 82 70 88 70 98 C70 88 80 82 92 82 C112 82 128 96 128 118 C128 140 100 170 74 205 Q70 210 66 205 Z"/></g>
  <g class="tile tile--blue" transform="translate(590,1342)">
    <rect class="frame" x="-13" y="-13" width="298" height="246" rx="34"/>
    <rect class="edge" width="272" height="220" rx="12"/><rect class="face" width="242" height="190" rx="12"/>
    <text class="label" x="250" y="50">Anthentia</text>
    <text class="symbol" x="18" y="196">A</text></g>
  <g class="tile tile--blue" transform="translate(892,1342)">
    <rect class="frame" x="-13" y="-13" width="298" height="246" rx="34"/>
    <rect class="edge" width="272" height="220" rx="12"/><rect class="face" width="242" height="190" rx="12"/>
    <text class="label" x="252" y="50">Hhmlita</text>
    <text class="symbol" x="24" y="196">H</text></g>
  <g class="tile tile--blue" transform="translate(1194,1342)">
    <rect class="frame" x="-13" y="-13" width="298" height="246" rx="34"/>
    <rect class="edge" width="272" height="220" rx="12"/><rect class="face" width="242" height="190" rx="12"/>
    <text class="label" x="256" y="50">Andacith</text>
    <text class="symbol" x="30" y="196">An</text></g>
  <g class="tile tile--blue" transform="translate(1496,1342)">
    <rect class="frame" x="-13" y="-13" width="298" height="246" rx="34"/>
    <rect class="edge" width="272" height="220" rx="12"/><rect class="face" width="242" height="190" rx="12"/>
    <text class="label" x="244" y="50">Justice</text>
    <text class="symbol" x="36" y="196">J</text></g>
</svg>
</body>
</html>
```